New tech executive consulting company needs professionally branded document templates

We are a new business selling fractional board advisory and go-to-market consulting services into the Technology space. Tessaly Brink are experts in providing high-quality executive-level leaders on a part-time basis to tech companies in need of their expertise. We work closely with clients to understand their business needs, challenges, and goals, and provides customised solutions to help them succeed. Due to our audience we need the design to have a high quality, executive look and feel.

Our first website is live and can be found at tessalybrink.example. We also already have a logo which I've uploaded. Our brand is clean and uses orange to give it colour and an identity that stands out.

We need some document master templates created so we can create our own presentations (Google Slides & Powerpoint), PDF documents, and Word templates, and ideally also a LinkedIn banner.

```html
<!DOCTYPE html>
<html lang="en">
<head>
<meta charset="utf-8">
<title>Tessaly Brink — Presentation Templates</title>
<link rel="stylesheet" href="https://fonts.googleapis.com/css2?family=Bebas+Neue&family=Montserrat:wght@400;500;600;700&display=swap">
<style>
:root{
  --navy:#29303b;
  --orange:#ee8650;
  --orange-soft:#f0a274;
  --page:#d1d2d4;
  --white:#ffffff;
  --ink:#2b2f36;
  --rule:#c9ccd1;
}
*{box-sizing:border-box;margin:0;padding:0}
html,body{width:777px;height:1200px;overflow:hidden;background:var(--page)}
body{position:relative;font-family:"Montserrat",Arial,sans-serif;color:var(--ink)}
.slide{position:absolute;width:277px;height:173px;background:var(--white);overflow:hidden;box-shadow:0 8px 8px -6px rgba(0,0,0,.35)}
.slide.dark{background:var(--navy)}
.col-l{left:88px}.col-r{left:412px}
.row1{top:105px}.row2{top:307px}.row3{top:507px}.row4{top:707px}.row5{top:907px}
.abs{position:absolute}
svg.fill{position:absolute;left:0;top:0;width:277px;height:173px}

.brand{position:absolute;font-family:"Montserrat",Arial,sans-serif;font-weight:700;letter-spacing:.5px;line-height:1.05;color:var(--navy);text-align:center}
.brand.on-dark{color:var(--white)}
.brand.lg{font-size:8.5px}
.brand.sm{font-size:3px;letter-spacing:.2px}

.cover-title{position:absolute;left:14px;top:62px;font-family:"Bebas Neue",Impact,sans-serif;font-size:22.5px;line-height:.9;color:var(--navy)}
.cover-title span{display:block;color:var(--orange)}
.dark .cover-title{color:var(--white)}
.cover-sub{position:absolute;left:14px;top:103px;font-size:6px;color:var(--navy)}
.dark .cover-sub{color:var(--white)}
.pill{position:absolute;left:13px;top:119px;background:var(--orange);color:var(--white);font-size:4.6px;padding:2px 5px;border-radius:5px}

.heading{position:absolute;left:8px;top:6px;font-family:"Bebas Neue",Impact,sans-serif;font-size:12.5px;color:var(--white);letter-spacing:.2px}
.footer-logo{left:14px;top:163px}

.body-copy{position:absolute;font-size:4.1px;line-height:1.9;text-align:justify;color:var(--ink)}
.body-copy p+p{margin-top:7px}
.small-copy{font-size:2.7px;line-height:1.3;color:var(--ink)}
.item-title{font-size:5px;color:var(--orange);font-weight:500}

.want-box{position:absolute;left:13px;top:59px;width:252px;height:78px;background:var(--navy)}
.want-label{position:absolute;left:116px;top:10px;font-family:"Bebas Neue",Impact,sans-serif;font-size:6px;color:var(--orange)}
.want-text{position:absolute;left:104px;top:18px;width:144px;font-size:3px;line-height:2.2;color:var(--white);text-align:justify}

.feature{position:absolute;width:118px;height:24px}
.feature .icon{position:absolute;left:0;top:3px;width:19px;height:19px;border-radius:50%;background:var(--orange)}
.feature .bar{position:absolute;left:23px;top:0;width:.6px;height:26px;background:var(--navy)}
.feature .txt{position:absolute;left:28px;top:0;width:94px}

.chart-items{position:absolute;left:173px;top:60px;width:86px}
.chart-items .it{margin-bottom:6.5px}

table.data{position:absolute;left:15px;top:49px;width:247px;border-collapse:collapse;font-size:3.3px}
table.data th{background:var(--navy);color:var(--white);font-weight:400;height:12px;line-height:1.2;text-align:center}
table.data th.first{text-align:left;padding-left:2px}
table.data td{height:11.2px;border-bottom:.5px solid var(--rule);text-align:center}
table.data td.first{text-align:left;padding-left:2px}
table.data th.hl{background:var(--orange)}
.hl-frame{position:absolute;left:91px;top:45px;width:43px;height:96px;border:.8px solid var(--orange);border-radius:4px}

.intro{position:absolute;left:10px;top:51px;width:257px;font-size:3.2px;line-height:1.25}
.tile{position:absolute;top:74px;width:75px}
.tile .ph{width:75px;height:36px}
.tile .h{margin-top:6px;text-align:center;font-size:5px;color:var(--orange);font-weight:500}
.tile ul{margin:6px 0 0 8px;font-size:3.1px;line-height:1.1;list-style:none}
.tile li{position:relative;padding-left:6px}
.tile li::before{content:"";position:absolute;left:0;top:1px;width:1.6px;height:1.6px;border-radius:50%;background:var(--orange)}

.member{position:absolute;top:64px;width:44px;text-align:center}
.member .avatar{width:29px;height:29px;margin:0 auto;border-radius:50%;background:var(--orange);border:2.5px solid var(--white);display:flex;align-items:center;justify-content:center}
.member .name{margin-top:6px;font-size:5.4px;font-weight:500;color:var(--navy)}
.member .bio{margin-top:1px;font-size:2.9px;line-height:1.25;text-align:justify}
.page-no{position:absolute;right:7px;top:162px;font-size:4px;border-left:.6px solid var(--orange);padding-left:2px}

.thanks{position:absolute;left:15px;top:56px;font-family:"Bebas Neue",Impact,sans-serif;font-size:30px;line-height:.88;color:var(--white)}
.thanks span{display:block;color:var(--orange)}
.contact{position:absolute;left:15px;top:125px;font-size:5.4px;line-height:1.8;color:var(--white)}
</style>
</head>
<body>

<!-- Cover, light -->
<section class="slide col-l row1">
  <svg class="fill" viewBox="0 0 277 173">
    <polygon points="229,0 277,0 277,173 121,173" fill="#8aa0a8" role="img" aria-label="Photo of a smiling businesswoman presenting at a meeting table"/>
    <polygon points="204,0 229,0 121,173 95,173" fill="var(--orange)"/>
  </svg>
  <div class="brand lg on-light" style="left:14px;top:16px">TESSALY<br>BRINK</div>
  <h1 class="cover-title">Presentation<span>Title Goeshere</span></h1>
  <p class="cover-sub">Subtitle of Presentation Goes Here</p>
  <span class="pill">www.tessalybrink.example</span>
</section>

<!-- Cover, dark -->
<section class="slide dark col-r row1">
  <svg class="fill" viewBox="0 0 277 173">
    <polygon points="229,0 277,0 277,173 121,173" fill="#8aa0a8" role="img" aria-label="Photo of a smiling businesswoman presenting at a meeting table"/>
    <polygon points="204,0 229,0 121,173 95,173" fill="var(--orange)"/>
  </svg>
  <div class="brand lg on-dark" style="left:14px;top:16px">TESSALY<br>BRINK</div>
  <h1 class="cover-title">Presentation<span>Title Goeshere</span></h1>
  <p class="cover-sub">Subtitle of Presentation Goes Here</p>
  <span class="pill">www.tessalybrink.example</span>
</section>

<!-- Text slide -->
<section class="slide col-l row2">
  <svg class="fill" viewBox="0 0 277 173">
    <rect x="98" y="0" width="179" height="26" fill="var(--orange)" role="img" aria-label="Orange tinted meeting photo banner"/>
    <polygon points="0,0 112,0 96,26 0,26" fill="var(--navy)"/>
    <line x1="0" y1="166" x2="14" y2="166" stroke="var(--navy)" stroke-width="1.4"/>
    <line x1="35" y1="166" x2="277" y2="166" stroke="var(--orange)" stroke-width="1.4"/>
  </svg>
  <h2 class="heading">Heading Goes Here</h2>
  <div class="body-copy" style="left:9px;top:48px;width:260px">
    <p>Lorem ipsum dolor sit amet, consectetuer adipiscing elit, sed diam nonummy nibh euismod tincidunt ut laoreet dolore magna aliquam erat volutpat. Ut wisi enim ad minim veniam, quis nostrud exerci tation ullamcorper suscipit lobortis nisl ut aliquip ex ea commodo consequat. Duis autem vel eum iriure dolor in hendrerit in vulputate velit esse molestie consequat, vel illum dolore eu feugiat nulla facilisis at vero eros et accumsan et iusto odio dignissim qui blandit praesent luptatum zzril delenit augue duis dolore te feugait nulla facilisi.</p>
    <p>Lorem ipsum dolor sit amet, cons ectetuer adipiscing elit, sed diam nonummy nibh euismod tincidunt ut laoreet dolore magna aliquam erat volutpat. Ut wisi enim ad minim veniam, quis nostrud exerci tation ullamcorper suscipit lobortis nisl ut aliquip ex ea commodo consequat.</p>
  </div>
  <div class="brand sm footer-logo abs" style="left:14px;top:163px">TESSALY<br>BRINK</div>
</section>

<!-- Photo + "You want" slide -->
<section class="slide col-r row2">
  <svg class="fill" viewBox="0 0 277 173">
    <rect x="98" y="0" width="179" height="26" fill="var(--orange)" role="img" aria-label="Orange tinted meeting photo banner"/>
    <polygon points="0,0 112,0 96,26 0,26" fill="var(--navy)"/>
    <line x1="0" y1="166" x2="14" y2="166" stroke="var(--navy)" stroke-width="1.4"/>
    <line x1="35" y1="166" x2="277" y2="166" stroke="var(--orange)" stroke-width="1.4"/>
  </svg>
  <h2 class="heading">Heading Goes Here</h2>
  <div class="want-box">
    <svg class="abs" style="left:0;top:0" width="252" height="78" viewBox="0 0 252 78">
      <polygon points="0,0 97,0 75,78 0,78" fill="#8fa3aa" role="img" aria-label="Photo of a team meeting in a bright office"/>
    </svg>
    <div class="want-label">You Want:</div>
    <div class="want-text">Lorem ipsum dolor sit amet, consectetuer adipiscing elit, sed diam nonummy nibh euismod tincidunt ut laoreet dolore magna aliquam erat volutpat. Ut lobortis nisl ut aliquip ex ea commodo consequat. Duis autem vel eum iriure dolor hendrerit in vulputate velit<br><br>esse molestie consequat, vel illum dolore eu feugiat nulla facilisis at vero eros et accumsan et iusto odio dignissim qui blandit praesent luptatum zzril delenit augue duis dolore te feugait nulla facilisi.</div>
  </div>
  <div class="brand sm abs" style="left:14px;top:163px">TESSALY<br>BRINK</div>
</section>

<!-- Four features slide -->
<section class="slide col-l row3">
  <svg class="fill" viewBox="0 0 277 173">
    <rect x="98" y="0" width="179" height="26" fill="var(--orange)" role="img" aria-label="Orange tinted meeting photo banner"/>
    <polygon points="0,0 112,0 96,26 0,26" fill="var(--navy)"/>
    <line x1="0" y1="166" x2="14" y2="166" stroke="var(--navy)" stroke-width="1.4"/>
    <line x1="35" y1="166" x2="277" y2="166" stroke="var(--orange)" stroke-width="1.4"/>
  </svg>
  <h2 class="heading">Heading Goes Here</h2>
  <div class="feature" style="left:13px;top:59px">
    <div class="icon"><svg width="19" height="19" viewBox="0 0 19 19"><circle cx="9.5" cy="6.5" r="2.3" fill="#fff"/><path d="M5 14.5c0-2.8 2-4.3 4.5-4.3s4.5 1.5 4.5 4.3z" fill="#fff"/></svg></div>
    <div class="bar"></div>
    <div class="txt"><div class="item-title">Title Goes Here</div><div class="small-copy">Lorem ipsum dolor sit amet, consectetuer adipiscing elit, sed diam nonummy nibh euismod tincidunt ut laoreet dolore magna aliquam erat volutpat. Ut wisi enim ad minim veniam, quis nostrud exerci tation ullamcorper suscipit lobortis nisl ut</div></div>
  </div>
  <div class="feature" style="left:143px;top:59px">
    <div class="icon"><svg width="19" height="19" viewBox="0 0 19 19"><circle cx="9.5" cy="6.5" r="2.3" fill="#fff"/><path d="M5 14.5c0-2.8 2-4.3 4.5-4.3s4.5 1.5 4.5 4.3z" fill="#fff"/></svg></div>
    <div class="bar"></div>
    <div class="txt"><div class="item-title">Title Goes Here</div><div class="small-copy">Lorem ipsum dolor sit amet, consectetuer adipiscing elit, sed diam nonummy nibh euismod tincidunt ut laoreet dolore magna aliquam erat volutpat. Ut wisi enim ad minim veniam, quis nostrud exerci tation ullamcorper suscipit lobortis nisl ut</div></div>
  </div>
  <div class="feature" style="left:13px;top:103px">
    <div class="icon"><svg width="19" height="19" viewBox="0 0 19 19"><circle cx="9.5" cy="6.5" r="2.3" fill="#fff"/><path d="M5 14.5c0-2.8 2-4.3 4.5-4.3s4.5 1.5 4.5 4.3z" fill="#fff"/></svg></div>
    <div class="bar"></div>
    <div class="txt"><div class="item-title">Title Goes Here</div><div class="small-copy">Lorem ipsum dolor sit amet, consectetuer adipiscing elit, sed diam nonummy nibh euismod tincidunt ut laoreet dolore magna aliquam erat volutpat. Ut wisi enim ad minim veniam, quis nostrud exerci tation ullamcorper suscipit lobortis nisl ut</div></div>
  </div>
  <div class="feature" style="left:143px;top:103px">
    <div class="icon"><svg width="19" height="19" viewBox="0 0 19 19"><circle cx="9.5" cy="6.5" r="2.3" fill="#fff"/><path d="M5 14.5c0-2.8 2-4.3 4.5-4.3s4.5 1.5 4.5 4.3z" fill="#fff"/></svg></div>
    <div class="bar"></div>
    <div class="txt"><div class="item-title">Title Goes Here</div><div class="small-copy">Lorem ipsum dolor sit amet, consectetuer adipiscing elit, sed diam nonummy nibh euismod tincidunt ut laoreet dolore magna aliquam erat volutpat. Ut wisi enim ad minim veniam, quis nostrud exerci tation ullamcorper suscipit lobortis nisl ut</div></div>
  </div>
  <div class="brand sm abs" style="left:14px;top:163px">TESSALY<br>BRINK</div>
</section>

<!-- Chart slide -->
<section class="slide col-r row3">
  <svg class="fill" viewBox="0 0 277 173">
    <rect x="98" y="0" width="179" height="26" fill="var(--orange)" role="img" aria-label="Orange tinted meeting photo banner"/>
    <polygon points="0,0 112,0 96,26 0,26" fill="var(--navy)"/>
    <polygon points="0,59 153,59 164,134 0,134" fill="var(--navy)"/>
    <g stroke="#ffffff" stroke-width=".4" opacity=".8">
      <line x1="19" y1="67" x2="140" y2="67"/><line x1="19" y1="74" x2="140" y2="74"/>
      <line x1="19" y1="81" x2="140" y2="81"/><line x1="19" y1="88" x2="140" y2="88"/>
      <line x1="19" y1="95" x2="140" y2="95"/><line x1="19" y1="102" x2="140" y2="102"/>
      <line x1="19" y1="109" x2="140" y2="109"/><line x1="19" y1="116" x2="140" y2="116"/>
      <line x1="19" y1="124" x2="141" y2="124"/>
      <line x1="19" y1="67" x2="19" y2="124"/><line x1="39" y1="67" x2="39" y2="124"/>
      <line x1="59" y1="67" x2="59" y2="124"/><line x1="79" y1="67" x2="79" y2="124"/>
      <line x1="99" y1="67" x2="99" y2="124"/><line x1="119" y1="67" x2="119" y2="124"/>
      <line x1="140" y1="67" x2="140" y2="124"/>
    </g>
    <circle cx="19" cy="66" r="1" fill="#fff"/><circle cx="142" cy="124" r="1" fill="#fff"/>
    <polyline points="29,124 38,104 44,90 59,84 75,113 85,124" fill="none" stroke="var(--orange)" stroke-width=".6"/>
    <polyline points="37,103 45,119 59,110 79,123 99,90 109,103 119,96 127,124" fill="none" stroke="var(--orange-soft)" stroke-width=".5"/>
    <polyline points="80,124 99,90 109,103 119,96 127,124" fill="none" stroke="#ffffff" stroke-width=".5"/>
    <line x1="0" y1="166" x2="14" y2="166" stroke="var(--navy)" stroke-width="1.4"/>
    <line x1="35" y1="166" x2="277" y2="166" stroke="var(--orange)" stroke-width="1.4"/>
  </svg>
  <h2 class="heading">Heading Goes Here</h2>
  <div class="chart-items">
    <div class="it"><div class="item-title">Title Goes Here</div><div class="small-copy">Lorem ipsum dolor sit amet, consectetuer adipiscing elit, sed diam nonummy nibh euismod tincidunt ut laoreet dolore magna aliquam erat volutpat. Ut wisi enim ad minim veniam, quis nostrud exerci tation ullamcorper suscipit lobortis nisl ut</div></div>
    <div class="it"><div class="item-title">Title Goes Here</div><div class="small-copy">Lorem ipsum dolor sit amet, consectetuer adipiscing elit, sed diam nonummy nibh euismod tincidunt ut laoreet dolore magna aliquam erat volutpat. Ut wisi enim ad minim veniam, quis nostrud exerci tation ullamcorper suscipit lobortis nisl ut</div></div>
    <div class="it"><div class="item-title">Title Goes Here</div><div class="small-copy">Lorem ipsum dolor sit amet, consectetuer adipiscing elit, sed diam nonummy nibh euismod tincidunt ut laoreet dolore magna aliquam erat volutpat. Ut wisi enim ad minim veniam, quis nostrud exerci tation ullamcorper suscipit lobortis nisl ut</div></div>
  </div>
  <div class="brand sm abs" style="left:14px;top:163px">TESSALY<br>BRINK</div>
</section>

<!-- Table slide -->
<section class="slide col-l row4">
  <svg class="fill" viewBox="0 0 277 173">
    <rect x="98" y="0" width="179" height="26" fill="var(--orange)" role="img" aria-label="Orange tinted meeting photo banner"/>
    <polygon points="0,0 112,0 96,26 0,26" fill="var(--navy)"/>
    <line x1="0" y1="166" x2="14" y2="166" stroke="var(--navy)" stroke-width="1.4"/>
    <line x1="35" y1="166" x2="277" y2="166" stroke="var(--orange)" stroke-width="1.4"/>
  </svg>
  <h2 class="heading">Heading Goes Here</h2>
  <table class="data">
    <colgroup><col style="width:76px"><col style="width:43px"><col style="width:43px"><col style="width:43px"><col style="width:42px"></colgroup>
    <thead><tr><th class="first">Heading Goes Here</th><th class="hl">Heading<br>Goes Here</th><th>Heading<br>Goes Here</th><th>Heading<br>Goes Here</th><th>Heading<br>Goes Here</th></tr></thead>
    <tbody>
      <tr><td class="first">Lorem Ipsum Goes Here</td><td>23</td><td>12</td><td>78</td><td>12</td></tr>
      <tr><td class="first">Lorem Ipsum Goes Here</td><td>45</td><td>56</td><td>12</td><td>56</td></tr>
      <tr><td class="first">Lorem Ipsum Goes Here</td><td>78</td><td>76</td><td>34</td><td>76</td></tr>
      <tr><td class="first">Lorem Ipsum Goes Here</td><td>22</td><td>12</td><td>55</td><td>12</td></tr>
      <tr><td class="first">Lorem Ipsum Goes Here</td><td>34</td><td>66</td><td>45</td><td>66</td></tr>
      <tr><td class="first">Lorem Ipsum Goes Here</td><td>67</td><td>47</td><td>78</td><td>47</td></tr>
      <tr><td class="first">Lorem Ipsum Goes Here</td><td>87</td><td>67</td><td>12</td><td>67</td></tr>
    </tbody>
  </table>
  <div class="hl-frame"></div>
  <div class="brand sm abs" style="left:14px;top:163px">TESSALY<br>BRINK</div>
</section>

<!-- Three tiles slide -->
<section class="slide col-r row4">
  <svg class="fill" viewBox="0 0 277 173">
    <rect x="98" y="0" width="179" height="26" fill="var(--orange)" role="img" aria-label="Orange tinted meeting photo banner"/>
    <polygon points="0,0 112,0 96,26 0,26" fill="var(--navy)"/>
    <line x1="0" y1="166" x2="14" y2="166" stroke="var(--navy)" stroke-width="1.4"/>
    <line x1="35" y1="166" x2="277" y2="166" stroke="var(--orange)" stroke-width="1.4"/>
  </svg>
  <h2 class="heading">Heading Goes Here</h2>
  <p class="intro">Northcrest Minerals Ltd (NX: NCM) is an exploration company with brownfield metals projects in the northern region. The Company's strategy is to develop a portfolio of projects that support the green economy through the discovery and delivery of commodities that promote electrification and decarbonisation. We seek to maximise shareholder value through the acquisition, discovery, and advancement of high quality precious, base, and strategic metal projects in the region.</p>
  <div class="tile" style="left:14px">
    <div class="ph" role="img" aria-label="Photo of colleagues working around an office table" style="background:linear-gradient(135deg,#5a6068,#c9ccd0)"></div>
    <div class="h">Heading Goes Here</div>
    <ul><li>Lorem ipsum dolar sit amet, consectetur adipiscing edit. Vivamus eu dui ex.</li></ul>
  </div>
  <div class="tile" style="left:102px">
    <div class="ph" role="img" aria-label="Photo of a businessman with a tablet and digital overlay" style="background:linear-gradient(135deg,#7fb0d6,#2f4d72)"></div>
    <div class="h">Heading Goes Here</div>
    <ul><li>Lorem ipsum dolar sit amet, consectetur adipiscing edit. Vivamus eu dui ex.</li></ul>
  </div>
  <div class="tile" style="left:190px">
    <div class="ph" role="img" aria-label="Photo of a team reviewing charts on a tablet" style="background:linear-gradient(135deg,#dfe6ee,#8ea7c2)"></div>
    <div class="h">Heading Goes Here</div>
    <ul><li>Lorem ipsum dolar sit amet, consectetur adipiscing edit. Vivamus eu dui ex.</li></ul>
  </div>
  <div class="brand sm abs" style="left:14px;top:163px">TESSALY<br>BRINK</div>
</section>

<!-- Team slide -->
<section class="slide col-l row5">
  <div class="abs" role="img" aria-label="Darkened photo of a team meeting" style="left:0;top:0;width:277px;height:79px;background:linear-gradient(180deg,#5e6a75 0%,#3a4350 60%,var(--navy) 100%)"></div>
  <div class="member" style="left:26px">
    <div class="avatar"><svg width="12" height="12" viewBox="0 0 12 12"><circle cx="6" cy="3.6" r="2.3" fill="#fff"/><path d="M1.5 11c0-3 2-4.5 4.5-4.5s4.5 1.5 4.5 4.5z" fill="#fff"/></svg></div>
    <div class="name">Name Here</div>
    <div class="bio">Lorem ipsum dolor sit amet, consectetuer adipiscing elit, sed diam nonummy nibh euismod tincidunt ut laoreet dolore magna aliquam erat volutpat. Ut wisi enim ad minim veniam, quis nostrud exerci tation</div>
  </div>
  <div class="member" style="left:86px">
    <div class="avatar"><svg width="12" height="12" viewBox="0 0 12 12"><circle cx="6" cy="3.6" r="2.3" fill="#fff"/><path d="M1.5 11c0-3 2-4.5 4.5-4.5s4.5 1.5 4.5 4.5z" fill="#fff"/></svg></div>
    <div class="name">Name Here</div>
    <div class="bio">Lorem ipsum dolor sit amet, consectetuer adipiscing elit, sed diam nonummy nibh euismod tincidunt ut laoreet dolore magna aliquam erat volutpat. Ut wisi enim ad minim veniam, quis nostrud exerci tation</div>
  </div>
  <div class="member" style="left:146px">
    <div class="avatar"><svg width="12" height="12" viewBox="0 0 12 12"><circle cx="6" cy="3.6" r="2.3" fill="#fff"/><path d="M1.5 11c0-3 2-4.5 4.5-4.5s4.5 1.5 4.5 4.5z" fill="#fff"/></svg></div>
    <div class="name">Name Here</div>
    <div class="bio">Lorem ipsum dolor sit amet, consectetuer adipiscing elit, sed diam nonummy nibh euismod tincidunt ut laoreet dolore magna aliquam erat volutpat. Ut wisi enim ad minim veniam, quis nostrud exerci tation</div>
  </div>
  <div class="member" style="left:206px">
    <div class="avatar"><svg width="12" height="12" viewBox="0 0 12 12"><circle cx="6" cy="3.6" r="2.3" fill="#fff"/><path d="M1.5 11c0-3 2-4.5 4.5-4.5s4.5 1.5 4.5 4.5z" fill="#fff"/></svg></div>
    <div class="name">Name Here</div>
    <div class="bio">Lorem ipsum dolor sit amet, consectetuer adipiscing elit, sed diam nonummy nibh euismod tincidunt ut laoreet dolore magna aliquam erat volutpat. Ut wisi enim ad minim veniam, quis nostrud exerci tation</div>
  </div>
  <div class="brand abs" style="left:8px;top:155px;font-size:4.6px">TESSALY<br>BRINK</div>
  <div class="page-no">07</div>
</section>

<!-- Thank you slide -->
<section class="slide dark col-r row5">
  <svg class="fill" viewBox="0 0 277 173">
    <polygon points="217,0 277,0 277,173 109,173" fill="#8aa0a8" role="img" aria-label="Photo of a smiling businesswoman presenting at a meeting table"/>
    <polygon points="206,0 227,0 119,173 95,173" fill="var(--orange)"/>
  </svg>
  <div class="brand lg on-dark" style="left:15px;top:16px">TESSALY<br>BRINK</div>
  <h2 class="thanks">Thank<span>You!</span></h2>
  <p class="contact">www.tessalybrink.example<br>+44 7700 900123<br>Mara Quint</p>
</section>

</body>
</html>
```